hotel's Website

Hotels website redesign for reference pictures, logo etc see http://restwellharbour.co.uk/

1. 2-3 Special offers on the main page.
2. Booking calender
3. Location Map
4. Picture gallery.
5. Journeymarks reviews.
6. short description
7. Social Media sharing.
8 Phone number and address.

Industry/Entity Type

Hotel

Requirements
Must have
• 1. 2-3 Special offers on the main page.
2. Booking calender
3. Location Map
4. Picture gallery.
5. Journeymarks reviews.
6. short description
7. Social Media sharing.

```html
<!DOCTYPE html>
<html lang="en">
<head>
<meta charset="utf-8">
<title>Restwell Harbour – Hotel in London</title>
<link rel="stylesheet" href="https://fonts.googleapis.com/css2?family=Sorts+Mill+Goudy&family=Open+Sans:wght@400;600;700&family=Oswald:wght@600&display=swap">
<style>
:root{
  --navy:#2b303b;
  --navy-deep:#1f232b;
  --blue:#0b68b2;
  --orange:#d6612f;
  --text:#6b6b6b;
  --light:#e9e9e9;
  --white:#ffffff;
  --line:#d8d8d8;
}
*{box-sizing:border-box;margin:0;padding:0}
html,body{width:1200px;height:2314px;overflow:hidden}
body{position:relative;background:var(--white);font-family:"Open Sans",Arial,sans-serif;color:var(--text)}
.abs{position:absolute}
.serif{font-family:"Sorts Mill Goudy",Georgia,serif;font-weight:400}
.section-title{position:absolute;left:200px;font-size:31px;color:#333;white-space:nowrap}

/* header */
.site-header{left:0;top:0;width:1200px;height:80px;background:linear-gradient(#ffffff,#ececec);border-bottom:1px solid #ddd}
.brand{left:200px;top:12px;width:54px;height:56px;background:var(--blue);color:#fff;font-family:"Sorts Mill Goudy",Georgia,serif;font-size:11px;line-height:13px;text-align:center;padding-top:16px}
.social-top{right:343px;top:13px;display:flex;gap:7px}
.social-top span{width:23px;height:23px;border-radius:50%;background:#2a2a2a;display:block}
.lang{left:944px;top:16px;width:57px;height:18px;border:1px solid #ccc;background:#f3f3f3;font-size:9px;line-height:16px;padding-left:6px;color:#555;white-space:nowrap}
.main-nav{right:200px;top:51px;display:flex;gap:30px;font-family:"Sorts Mill Goudy",Georgia,serif;font-size:12.5px;color:#666;white-space:nowrap}
.main-nav .active{color:#222}

/* hero */
.hero{left:0;top:80px;width:1200px;height:398px;background:linear-gradient(135deg,#6b4a2c 0%,#b8926a 30%,#d9c1a0 55%,#8a5b36 80%,#5a3a22 100%)}
.hero-arrow{top:120px}
.hero-caption{left:213px;top:170px;width:375px;height:134px;background:rgba(40,44,52,.85);padding:12px 10px}
.hero-caption h1{font-size:31px;line-height:34px;color:#fff}
.hero-caption p{font-size:17px;color:#ddd;line-height:22px;margin-top:4px}
.btn{display:inline-block;background:var(--blue);color:#fff;font-weight:700;text-align:center;white-space:nowrap}
.hero-caption .btn{font-size:11px;padding:4px 10px;margin-top:8px}

/* booking */
.booking{left:0;top:478px;width:1200px;height:242px;background:var(--navy)}
.booking .section-title{color:#fff;top:20px;left:200px}
.where{left:200px;top:75px;width:800px;height:38px;background:#5a5e67}
.where .tag{width:78px;height:38px;background:var(--blue);color:#fff;font-size:13px;line-height:38px;text-align:center;float:left}
.where .field{float:left;font-size:11px;color:#c8c8c8;line-height:38px;padding-left:12px}
.field-row{left:200px;top:131px;width:800px;height:36px;display:flex;gap:7px}
.field-group{display:flex;height:36px;flex:none}
.field-group .label{flex:none;background:var(--orange);color:#fff;font-size:12px;line-height:36px;text-align:center;white-space:nowrap}
.field-group .value{flex:none;background:#fff;color:var(--orange);font-size:11px;line-height:36px;padding:0 10px;position:relative;white-space:nowrap}
.field-group .value:after{content:"";position:absolute;right:8px;top:15px;border:5px solid transparent;border-top:6px solid #333}
.search-btn{left:551px;top:180px;width:99px;height:36px;font-size:16px;line-height:36px;border-bottom:3px solid #084d86}

/* offers */
.offers .section-title{top:748px}
.offer{top:796px;height:175px;border:1px solid var(--line);text-align:center}
.offer .head{height:37px;color:#fff;font-size:17px;line-height:37px;font-family:"Sorts Mill Goudy",Georgia,serif;white-space:nowrap}
.offer .detail{position:absolute;left:50%;transform:translateX(-50%);bottom:10px;width:80px;height:29px;background:var(--navy);color:#fff;font-weight:700;font-size:13px;line-height:29px}
.discount{position:absolute;left:34px;top:14px;display:flex;align-items:flex-start;font-family:"Oswald",Impact,sans-serif;font-weight:600}
.discount .num{font-size:104px;line-height:104px;color:var(--blue);letter-spacing:-4px}
.discount .rest{display:flex;flex-direction:column;margin-left:4px;margin-top:10px}
.discount .off{font-size:50px;line-height:48px;color:var(--navy)}
.discount .small{font-size:8px;color:#555;font-family:"Open Sans",sans-serif;font-weight:400;white-space:nowrap}
.discount .fees{font-size:36px;line-height:38px;color:var(--orange)}
.offer-photo{position:absolute;left:0;top:37px;width:100%;height:136px;background:linear-gradient(160deg,#5a3b30,#8c6a55 50%,#3a2a24)}
.offer-photo p{color:#fff;font-size:12px;line-height:17px;padding:12px 18px}
.offer .list{font-size:12.5px;line-height:17px;color:#777;padding-top:9px}
.offer .list .dates{color:var(--blue)}

/* welcome */
.divider{left:0;top:1002px;width:1200px;border-top:1px dotted #ccc}
.welcome{left:200px;top:1026px;width:800px;text-align:center}
.welcome h2{font-size:32px;color:#333}
.welcome h2 span{color:var(--blue)}
.welcome p{font-size:12.5px;line-height:17px;margin-top:8px;color:#777}
.read-more{left:551px;top:1153px;width:99px;height:37px;font-size:13px;line-height:37px}

/* gallery */
.gallery{left:0;top:1221px;width:1200px;height:602px;background:var(--light)}
.gallery .section-title{top:28px}
.gallery-main{left:324px;top:80px;width:551px;height:349px;background:radial-gradient(ellipse at 50% 60%,#d9c98a,#b49a5a 45%,#6a5a3a 100%)}
.gallery-caption{left:324px;top:429px;width:551px;height:40px;background:var(--navy);color:#fff;font-size:15px;line-height:40px;text-align:center}
.gallery-arrow{top:220px}
.thumbs{left:200px;top:484px;width:800px;display:flex;gap:7px}
.thumbs span{width:155px;height:85px;display:block}

/* reviews & map */
.reviews .section-title{top:1850px}
.map-title{left:615px;top:1850px}
.review{left:200px;width:386px;height:100px}
.review .avatar{position:absolute;left:0;top:0;width:71px;height:71px;border:1px solid #bbb;background:linear-gradient(#9a8a7a,#5a4a3a)}
.review .quote{position:absolute;left:78px;top:-6px;font-family:Georgia,serif;font-size:40px;color:#333}
.review .quote.end{left:342px;top:24px}
.review p{position:absolute;left:101px;top:6px;width:285px;font-size:12px;line-height:16px;color:#555}
.review .name{position:absolute;left:101px;top:50px;font-size:12px;color:var(--blue)}
.review-sep{left:200px;top:1990px;width:386px;border-top:1px solid #e2e2e2}
.map{left:615px;top:1901px;width:386px;height:175px;border:1px solid #9fb3c8;background:linear-gradient(120deg,#c9dcef 0%,#dfe8d0 35%,#e8e2cf 60%,#c9dcef 100%)}

/* footer */
.site-footer{left:0;top:2108px;width:1200px;height:171px;background:var(--navy)}
.footer-col{top:20px;color:#bfc3ca;font-size:10px;line-height:16px}
.footer-col h3{color:#fff;font-size:13.5px;font-weight:400;margin-bottom:8px;white-space:nowrap}
.footer-col ul{list-style:none}
.footer-col li{display:flex;align-items:center;gap:8px;white-space:nowrap}
.follow li{margin-bottom:7px}
.follow li span{width:17px;height:17px;border-radius:50%;background:#5b606a;display:block}
.contact li svg{flex:none}
.bottom-bar{left:0;top:2279px;width:1200px;height:35px;background:var(--navy-deep);color:#7d828a;font-size:9.5px;line-height:35px;text-align:center}
</style>
</head>
<body>

<header class="site-header abs">
  <div class="brand abs">Restwell<br>Harbour</div>
  <div class="social-top abs" aria-label="Social links"><span></span><span></span><span></span><span></span><span></span></div>
  <div class="lang abs">English ▾</div>
  <nav class="main-nav abs">
    <span class="active">Home</span><span>Our Rooms</span><span>London Events</span><span>Booking</span><span>Special Offers</span><span>Photos</span><span>Contact</span>
  </nav>
</header>

<section class="hero abs" role="img" aria-label="Hotel suite lounge with armchairs, table and flowers">
  <svg class="hero-arrow abs" style="left:168px" width="24" height="70" viewBox="0 0 24 70"><path d="M22 2 L2 35 L22 68" fill="none" stroke="#fff" stroke-width="2" opacity=".7"/></svg>
  <svg class="hero-arrow abs" style="left:1008px" width="24" height="70" viewBox="0 0 24 70"><path d="M2 2 L22 35 L2 68" fill="none" stroke="#fff" stroke-width="2" opacity=".7"/></svg>
  <div class="hero-caption abs">
    <h1 class="serif">Stay in Comfort</h1>
    <p>Enjoy your time in London in our spacious suites.</p>
    <span class="btn">Book Now</span>
  </div>
</section>

<section class="booking abs">
  <h2 class="section-title serif">Booking calender</h2>
  <div class="where abs">
    <div class="tag">Where</div>
    <div class="field">City, region or specific hotel...</div>
    <svg class="abs" style="right:10px;top:10px" width="19" height="19" viewBox="0 0 19 19"><circle cx="7.5" cy="7.5" r="6" fill="none" stroke="#fff" stroke-width="2"/><path d="M12 12 L18 18" stroke="#fff" stroke-width="2.5"/></svg>
  </div>
  <div class="field-row abs">
    <div class="field-group"><span class="label" style="width:77px">Check In</span><span class="value" style="width:166px">Sat 15th, Des 2013</span></div>
    <div class="field-group"><span class="label" style="width:79px">Check Out</span><span class="value" style="width:179px">Tue 22th, Des 2013</span></div>
    <div class="field-group"><span class="label" style="width:68px">Guests</span><span class="value" style="width:66px">2</span></div>
    <div class="field-group"><span class="label" style="width:69px">Rooms</span><span class="value" style="width:74px">1</span></div>
  </div>
  <span class="search-btn btn abs">Search</span>
</section>

<section class="offers">
  <h2 class="section-title serif">Special Offers</h2>
  <article class="offer abs" style="left:200px;width:262px">
    <div class="discount"><span class="num">25</span><span class="rest"><span class="off">off</span><span class="small">Spa Treatments</span><span class="fees">FEES</span></span></div>
    <span class="detail">Detail</span>
  </article>
  <article class="offer abs" style="left:469px;width:261px">
    <div class="head" style="background:var(--orange)">Explore London</div>
    <div class="offer-photo" role="img" aria-label="Hotel interior with warm lighting">
      <p>London is one of the culture capitals of the world and is brimming with exciting things to see and do. Come and stay at our hotel to experience it!</p>
    </div>
    <span class="detail" style="background:#fff;color:#333">Detail</span>
  </article>
  <article class="offer abs" style="left:738px;width:262px">
    <div class="head" style="background:var(--blue);font-size:16px">Enjoy Our Special Summer Offers</div>
    <div class="list">Minimum 3 Nights Stay<br>During the Period<br><span class="dates">26/11/2013 - 26/12/2013</span><br>Pay Bed &amp; Breakfast<br>Stay Half Board Plus</div>
    <span class="detail">Detail</span>
  </article>
</section>

<div class="divider abs"></div>

<section class="welcome abs">
  <h2 class="serif">Welcome to <span>Restwell Harbour</span></h2>
  <p>Lorem ipsum dolor sit amet, consectetur adipiscing elit. Duis vitae nibh ut urna rutrum interdum eu eget orci. Cras venenatis vulputate lectus, sit amet dapibus orci mattis in. Pellentesque habitant morbi tristique senectus et netus et malesuada fames ac turpis egestas. Pellentesque euismod lacus eu ipsum molestie, ut tempus urna laoreet. Nam nisl mauris, vestibulum sit amet ligula a, sollicitudin mattis nulla.</p>
</section>
<span class="read-more btn abs">Read More</span>

<section class="gallery abs">
  <h2 class="section-title serif">Picture Gallery</h2>
  <svg class="gallery-arrow abs" style="left:252px" width="40" height="80" viewBox="0 0 40 80"><path d="M38 2 L2 40 L38 78" fill="none" stroke="#fff" stroke-width="2"/></svg>
  <svg class="gallery-arrow abs" style="left:908px" width="40" height="80" viewBox="0 0 40 80"><path d="M2 2 L38 40 L2 78" fill="none" stroke="#fff" stroke-width="2"/></svg>
  <div class="gallery-main abs" role="img" aria-label="Grand hotel atrium with chandelier and balconies"></div>
  <div class="gallery-caption abs">Lorem Ipsum Dolor as Sit Amet</div>
  <div class="thumbs abs">
    <span role="img" aria-label="Hotel hall" style="background:linear-gradient(#7a6a4a,#3a3020)"></span>
    <span role="img" aria-label="Pool lounge" style="background:linear-gradient(#3a4a6a,#8aa0b8)"></span>
    <span role="img" aria-label="Hotel exterior at dusk" style="background:linear-gradient(#2a4a8a,#c8d4e8)"></span>
    <span role="img" aria-label="Hotel facade at night" style="background:linear-gradient(#2a2030,#a8784a)"></span>
    <span role="img" aria-label="Hotel lobby" style="background:linear-gradient(#3a2818,#9a6a3a)"></span>
  </div>
</section>

<section class="reviews">
  <h2 class="section-title serif">Journeymarks Reviews</h2>
  <div class="review abs" style="top:1904px">
    <div class="avatar" role="img" aria-label="Guest photo"></div>
    <span class="quote">“</span>
    <p>Lorem ipsum dolor sit amet, consectetur adipiscing elit. Praesent semper velit at orci pharetra.</p>
    <span class="quote end">”</span>
    <span class="name">Mara Ellis</span>
  </div>
  <div class="review-sep abs"></div>
  <div class="review abs" style="top:2006px">
    <div class="avatar" role="img" aria-label="Guest photo"></div>
    <span class="quote">“</span>
    <p>Lorem ipsum dolor sit amet, consectetur adipiscing elit. Praesent semper velit at orci pharetra.</p>
    <span class="quote end">”</span>
    <span class="name">Tomas Reed</span>
  </div>
  <h2 class="section-title serif map-title">Location Map</h2>
  <div class="map abs" role="img" aria-label="Road map showing the hotel location"></div>
</section>

<footer class="site-footer abs">
  <div class="footer-col abs" style="left:200px">
    <h3>Navigation</h3>
    <ul><li>Home</li><li>Our Rooms</li><li>London Events</li><li>Booking</li><li>Special Offers</li><li>Photos</li><li>Contact</li></ul>
  </div>
  <div class="footer-col abs" style="left:390px;width:220px">
    <h3>About Us</h3>
    <p>Lorem ipsum dolor sit amet, consectetur adipiscing elit. Praesent semper velit at orci elementum pharetra. Nullam feugiat magna sit amet ante fringilla hendrerit. Mauris lacinia ante nulla, sed ornare sem consequat et. Ut fringilla est mattis, conse quat urna vitae, vestibulum nulla.</p>
  </div>
  <div class="footer-col follow abs" style="left:697px">
    <h3>Follow Us</h3>
    <ul><li><span></span>Friendwall</li><li><span></span>Chirper</li><li><span></span>Circles</li><li><span></span>Journeymarks</li><li><span></span>Pinboard</li></ul>
  </div>
  <div class="footer-col contact abs" style="left:895px">
    <h3>Contact Us</h3>
    <ul>
      <li><svg width="10" height="10" viewBox="0 0 10 10"><path d="M2 1 L4 1 L4.5 3 L3.3 4 Q4.5 6 6 6.7 L7 5.5 L9 6 L9 8 Q5 9 1 2 Z" fill="#8b9099"/></svg>0800-555-0142</li>
      <li><svg width="10" height="10" viewBox="0 0 10 10"><rect x="1" y="1" width="8" height="8" fill="#8b9099"/><rect x="3" y="3" width="4" height="1" fill="#2b303b"/><rect x="3" y="5" width="4" height="1" fill="#2b303b"/></svg>0800-555-0142</li>
      <li><svg width="10" height="10" viewBox="0 0 10 10"><rect x="0.5" y="2" width="9" height="6" fill="#8b9099"/><path d="M0.5 2 L5 5.5 L9.5 2" fill="none" stroke="#2b303b"/></svg>info@restwellharbour.co.uk</li>
    </ul>
  </div>
</footer>
<div class="bottom-bar abs">© 2012–2013 Restwell Harbour &nbsp;|&nbsp; Terms &amp; Conditions &nbsp;|&nbsp; Privacy Policy</div>

</body>
</html>
```